Business Intelligence Application - Reporting Menu and Report Criteria Design

Looking for a fresh, effective and user friendly view for the menu structure and reporting criteria screen format for a business reporting application. Initial format completed, content structure is in place, but we need the 'wow' design.. as its a serious professional report/BI tool it has to fall within certain guidelines for clarity and graphics..but we want it to be slick, friendly, great user experience. There is a large amount of complex content to fit into a small space and we need it to be very inviting, modern and intuitive.. If interested, please review the attachment. We have live screens in operation, but feel these could be improved and looking forward to seeing what great creative suggestions could be made. Please review work done to date in the attached.. We are not looking for a total re-design of everything, all the basic business content/structure is there.. but tell us what we could do to improve this in terms of graphic design... particularly the criteria screens.. thanks!
Updates

Reason: Need a few more days to review designs - thanks for all submissions so far, we will make a selection shortly.

Target Market(s)

Business analysts, hotel operations teams, finance analysts hospitality industry

Industry/Entity Type

Hospitality

Coding

Coded - Design and coding required

Number of Pages Required

4 page

Font styles to use
Sans Serif
Other font styles liked:
• Candara, please see example in deck

Colors
3276b5
3176b5
0255a3
85acd3
33a6d7
cee9f5
85cae6

Requirements
Must have
• sharp clear, logical menu structure, (currently it has 'clicks to sub-menus, we need hover over, slide to sub-menus..) colour, styling.. and most focus on revision of criteria.. right now is somewhat heavy, cumbersome.. keep colour and friendly intuitive process steps.. its heavy analytical stuff.. best of luck!
Should not have
• No grey fonts on white or grey screens! many business apps are not readable or sharp.. or fonts are too small.. colourless, so please avoid that.. see our deck - sharp dark (navy) or black fonts on white, or light shading..

```html
<!DOCTYPE html>
<html lang="en">
<head>
<meta charset="utf-8">
<title>Lumora – Admin Menu</title>
<link href="https://fonts.googleapis.com/css2?family=Montserrat:wght@500;600;700&family=Nunito:wght@400&family=Open+Sans:wght@400;600&display=swap" rel="stylesheet">
<style>
  :root{
    --navy:#021a3a;
    --sky:#33a6d7;
    --royal:#0255a3;
    --steel:#3176b5;
    --steel-2:#3276b5;
    --ice:#cee9f5;
    --panel-head:#b3dcef;
    --line:#85cae6;
    --line-dark:#85acd3;
    --white:#ffffff;
    --ink:#0255a3;
    --muted:#8a8a8a;
    --field-border:#dcdcdc;
  }
  *{box-sizing:border-box;margin:0;padding:0}
  html,body{width:1200px;height:738px;overflow:hidden;background:var(--white)}
  body{position:relative;font-family:"Montserrat",sans-serif}

  .brand-bar{position:absolute;left:0;top:0;width:300px;height:89px;background:var(--navy);display:flex;align-items:center;padding-left:62px;gap:10px}
  .brand-bar .mark{width:22px;height:22px;border-radius:50%;background:var(--sky)}
  .brand-bar .name{color:var(--white);font-weight:600;font-size:21px;letter-spacing:.2px}

  .topbar{position:absolute;left:300px;top:0;width:900px;height:89px;background:var(--ice)}
  .search{position:absolute;left:32px;top:20px;width:514px;height:47px;background:var(--white);border-radius:2px}
  .search .avatar{position:absolute;right:8px;top:8px;width:31px;height:31px;border-radius:50%;background:radial-gradient(circle at 50% 55%,#c79a6a 0 45%,#6b3f22 46%);border:2px solid #f1e6da}
  .user{position:absolute;left:570px;top:20px;width:48px;height:48px;border-radius:50%;border:2px solid var(--navy);display:flex;align-items:center;justify-content:center}
  .welcome{position:absolute;left:634px;top:26px;color:var(--royal);font-weight:600;font-size:11.5px}
  .date{position:absolute;left:634px;top:47px;color:var(--navy);font-style:italic;font-size:11.5px;font-weight:500}
  .top-icon{position:absolute;top:37px}

  .sidebar{position:absolute;left:0;top:89px;width:300px;height:649px;background:var(--sky)}
  .menu{position:absolute;left:0;top:26px;width:300px;list-style:none}
  .menu li,.sub li{position:relative;height:49px;display:flex;align-items:center;color:var(--white);font-weight:600;font-size:12px;letter-spacing:.3px}
  .menu li{padding-left:94px;border-bottom:1px dashed var(--line)}
  .menu li::before{content:"";position:absolute}
  .menu li.active{background:var(--royal);border-bottom-color:transparent}
  .menu li:last-child{border-bottom:none}
  .menu .ico{position:absolute;left:60px;top:18px}
  .menu .chev{position:absolute;left:259px;top:20px}
  .menu li:not(.active){margin-left:57px;padding-left:37px}
  .menu li:not(.active) .ico{left:3px}
  .menu li:not(.active) .chev{left:202px}
  .copyright{position:absolute;left:76px;top:582px;color:var(--white);font-size:12px;font-weight:500;line-height:21px}

  .sub{position:absolute;list-style:none}
  .sub-level-1{left:300px;top:115px;width:215px;background:var(--royal)}
  .sub-level-1 li{padding-left:49px;border-bottom:1px dashed var(--line-dark)}
  .sub-level-1 li:last-child{border-bottom:none}
  .sub-level-1 li.current{background:var(--steel)}
  .sub-level-1 .ico{position:absolute;left:16px;top:18px}
  .sub-level-1 .chev{position:absolute;left:180px;top:20px}
  .sub-level-2{left:515px;top:214px;width:215px;background:var(--steel-2);padding-bottom:3px}
  .sub-level-2 li{padding-left:18px;border-bottom:1px dashed var(--line-dark);margin-right:3px}
  .sub-level-2 li:last-child{border-bottom:none}

  .filters{position:absolute;top:116px;height:43px}
  .field{position:absolute;top:116px;height:43px;border:2px solid var(--field-border);background:var(--white);font-family:"Nunito",sans-serif;font-size:13px;color:var(--muted);display:flex;align-items:center;padding-left:13px}
  .field .caret{position:absolute;right:12px;top:16px}

  .panel{position:absolute;left:330px;top:202px;width:809px;height:248px;border:1px solid #e6e6e6}
  .panel-head{height:44px;background:var(--panel-head);position:relative}
  .panel-head svg{position:absolute;top:15px}
  .rows{position:relative;height:204px;font-family:"Open Sans",sans-serif;font-size:14px;letter-spacing:.3px;color:#b0b0b0}
  .row{position:absolute;left:0;width:785px;display:flex;align-items:center;padding-left:17px}
  .row:nth-child(even){background:#f8f8f8}
  .row .link{color:var(--line-dark)}
  .row .code{position:absolute;left:715px}
  .scroll{position:absolute;right:0;top:0;width:23px;height:204px;background:#f1f1f1}
</style>
</head>
<body>

<div class="brand-bar"><span class="mark"></span><span class="name">Lumora</span></div>

<header class="topbar">
  <div class="search"><span class="avatar" role="img" aria-label="User avatar picture"></span></div>
  <div class="user">
    <svg width="20" height="20" viewBox="0 0 20 20"><circle cx="10" cy="6" r="4.5" fill="#0255a3"/><path d="M2 19c0-5 4-7 8-7s8 2 8 7z" fill="#0255a3"/></svg>
  </div>
  <div class="welcome">WELCOME ADMIN</div>
  <div class="date">Tuesday Oct 3, 2017</div>
  <svg class="top-icon" style="left:790px" width="14" height="15" viewBox="0 0 14 15"><path d="M7 1c-3 0-4.5 2.5-4.5 5v3L1 11h12l-1.5-2V6C11.5 3.5 10 1 7 1z" fill="#0255a3"/><circle cx="7" cy="13" r="1.6" fill="#0255a3"/></svg>
  <svg class="top-icon" style="left:825px" width="14" height="13" viewBox="0 0 14 13"><path d="M1 2h5v2H3v5h3v2H1z" fill="#0255a3"/><path d="M6 5h4V2l4 4.5L10 11V8H6z" fill="#0255a3"/></svg>
</header>

<nav class="sidebar">
  <ul class="menu">
    <li class="active">
      <svg class="ico" width="11" height="12" viewBox="0 0 11 12"><circle cx="5.5" cy="3" r="2.8" fill="#fff"/><path d="M0 12c0-4 2.5-5.5 5.5-5.5S11 8 11 12z" fill="#fff"/></svg>
      ADMIN
      <svg class="chev" width="8" height="6" viewBox="0 0 8 6"><path d="M1 1l3 3 3-3" stroke="#fff" stroke-width="1.3" fill="none"/></svg>
    </li>
    <li>
      <svg class="ico" width="14" height="11" viewBox="0 0 14 11"><circle cx="7" cy="3" r="2.5" fill="#fff"/><circle cx="2.5" cy="4" r="1.8" fill="#fff"/><circle cx="11.5" cy="4" r="1.8" fill="#fff"/><path d="M3 11c0-3 2-4.5 4-4.5s4 1.5 4 4.5z" fill="#fff"/><path d="M0 10c0-2 1-3 2.5-3s2 .6 2 1V10z M14 10c0-2-1-3-2.5-3s-2 .6-2 1V10z" fill="#fff"/></svg>
      MANAGEMENT
      <svg class="chev" width="6" height="8" viewBox="0 0 6 8"><path d="M1 1l3 3-3 3" stroke="#fff" stroke-width="1.3" fill="none"/></svg>
    </li>
    <li>
      <svg class="ico" width="12" height="12" viewBox="0 0 12 12"><circle cx="5" cy="5" r="3.5" stroke="#fff" stroke-width="1.8" fill="none"/><path d="M7.5 7.5L11 11" stroke="#fff" stroke-width="2"/></svg>
      PROPERTY SEARCH
      <svg class="chev" width="6" height="8" viewBox="0 0 6 8"><path d="M1 1l3 3-3 3" stroke="#fff" stroke-width="1.3" fill="none"/></svg>
    </li>
    <li>
      <svg class="ico" width="12" height="12" viewBox="0 0 12 12"><circle cx="6" cy="6" r="4.2" fill="none" stroke="#fff" stroke-width="2.6" stroke-dasharray="2.2 1.1"/><circle cx="6" cy="6" r="1.5" fill="#fff"/></svg>
      INTEL
      <svg class="chev" width="6" height="8" viewBox="0 0 6 8"><path d="M1 1l3 3-3 3" stroke="#fff" stroke-width="1.3" fill="none"/></svg>
    </li>
    <li>
      <svg class="ico" width="10" height="12" viewBox="0 0 10 12"><path d="M0 0h6.5L10 3.5V12H0z" fill="#fff"/><path d="M2 6h6M2 8h6M2 10h6" stroke="#33a6d7" stroke-width=".9"/></svg>
      PLANNING
      <svg class="chev" width="6" height="8" viewBox="0 0 6 8"><path d="M1 1l3 3-3 3" stroke="#fff" stroke-width="1.3" fill="none"/></svg>
    </li>
  </ul>
  <p class="copyright">Copyright © 2017. Company Name<br>All Right Reserved</p>
</nav>

<div class="field" style="left:489px;width:106px;padding-left:30px">n ID</div>
<div class="field" style="left:606px;width:124px">Search Product</div>
<div class="field" style="left:741px;width:125px">Divisions<svg class="caret" width="8" height="6" viewBox="0 0 8 6"><path d="M1 1l3 3 3-3" stroke="#999" stroke-width="1.1" fill="none"/></svg></div>
<div class="field" style="left:877px;width:125px">Regions<svg class="caret" width="8" height="6" viewBox="0 0 8 6"><path d="M1 1l3 3 3-3" stroke="#999" stroke-width="1.1" fill="none"/></svg></div>
<div class="field" style="left:1014px;width:125px">Areas<svg class="caret" width="8" height="6" viewBox="0 0 8 6"><path d="M1 1l3 3 3-3" stroke="#999" stroke-width="1.1" fill="none"/></svg></div>

<section class="panel">
  <div class="panel-head">
    <svg style="left:732px" width="16" height="16" viewBox="0 0 16 16"><path d="M13 6A5.5 5.5 0 0 0 3 5M3 10a5.5 5.5 0 0 0 10 1" stroke="#fff" stroke-width="2.2" fill="none"/><path d="M14 1v5.5H8.5zM2 15V9.5h5.5z" fill="#fff"/></svg>
    <svg style="left:786px" width="13" height="13" viewBox="0 0 13 13"><path d="M2 2l9 9M11 2l-9 9" stroke="#fff" stroke-width="2.6"/></svg>
  </div>
  <div class="rows">
    <div class="row" style="top:0;height:59px"><span class="code" style="color:#a8a8a8">RHDOH</span></div>
    <div class="row" style="top:59px;height:49px">Coral Bay Hotel<span class="code">123</span></div>
    <div class="row" style="top:108px;height:49px"><span class="link">Harbour View Hotel &amp; T</span><span class="code">RHDOH</span></div>
    <div class="row" style="top:157px;height:47px">Coral Bay Hotel<span class="code">123</span></div>
    <div class="scroll">
      <svg style="position:absolute;left:8px;top:9px" width="7" height="5" viewBox="0 0 7 5"><path d="M0 5l3.5-5L7 5z" fill="#b5b5b5"/></svg>
      <svg style="position:absolute;left:8px;top:189px" width="7" height="5" viewBox="0 0 7 5"><path d="M0 0l3.5 5L7 0z" fill="#b5b5b5"/></svg>
    </div>
  </div>
</section>

<ul class="sub sub-level-1">
  <li>
    <svg class="ico" width="11" height="12" viewBox="0 0 11 12"><circle cx="5.5" cy="3" r="2.8" fill="#fff"/><path d="M0 12c0-4 2.5-5.5 5.5-5.5S11 8 11 12z" fill="#fff"/></svg>
    REGISTRATION
    <svg class="chev" width="6" height="8" viewBox="0 0 6 8"><path d="M1 1l3 3-3 3" stroke="#fff" stroke-width="1.3" fill="none"/></svg>
  </li>
  <li>
    <svg class="ico" width="14" height="11" viewBox="0 0 14 11"><circle cx="7" cy="3" r="2.5" fill="#fff"/><circle cx="2.5" cy="4" r="1.8" fill="#fff"/><circle cx="11.5" cy="4" r="1.8" fill="#fff"/><path d="M3 11c0-3 2-4.5 4-4.5s4 1.5 4 4.5z" fill="#fff"/></svg>
    USER ACCESS
    <svg class="chev" width="6" height="8" viewBox="0 0 6 8"><path d="M1 1l3 3-3 3" stroke="#fff" stroke-width="1.3" fill="none"/></svg>
  </li>
  <li class="current">
    <svg class="ico" width="12" height="12" viewBox="0 0 12 12"><circle cx="5" cy="5" r="3.5" stroke="#fff" stroke-width="1.8" fill="none"/><path d="M7.5 7.5L11 11" stroke="#fff" stroke-width="2"/></svg>
    SET UP
    <svg class="chev" width="6" height="8" viewBox="0 0 6 8"><path d="M1 1l3 3-3 3" stroke="#fff" stroke-width="1.3" fill="none"/></svg>
  </li>
  <li>
    <svg class="ico" width="12" height="12" viewBox="0 0 16 16"><path d="M13 6A5.5 5.5 0 0 0 3 5M3 10a5.5 5.5 0 0 0 10 1" stroke="#fff" stroke-width="2.2" fill="none"/><path d="M14 1v5.5H8.5zM2 15V9.5h5.5z" fill="#fff"/></svg>
    DATA IMPORT
    <svg class="chev" width="6" height="8" viewBox="0 0 6 8"><path d="M1 1l3 3-3 3" stroke="#fff" stroke-width="1.3" fill="none"/></svg>
  </li>
</ul>

<ul class="sub sub-level-2">
  <li>MARKET SEGMENT</li>
  <li>BENQUET &amp; CATERING</li>
  <li>OUTLETS F&amp;B&nbsp; SERVICE</li>
  <li>OTHER INCOME</li>
  <li>IMPACT DATES</li>
  <li>INVENTORY</li>
  <li>GEO/LOCATION</li>
  <li>DISTRIBUTION CHANNELS</li>
</ul>

</body>
</html>
```